Road Construction Company needs business cards

We would like a new business card designed for our business.

We're a road construction company based in Qld, Australia.

Can the business card please have the following information on it.

Name: Warren Halbeck
Position: General Manager
Phone: 0472 915 348
Email: Warren.halbeck@tovrin.com.au
Address: 87 Marrow Ave, Pendlebay, QLD, 4023
Website: www.tovrin.com.au

Visually we'd like the card to be professional and simple.

Attached is our logo.

Our website is www.tovrin.com.au

Target Market(s)

Men aged 25-60

Contact Information for Business Card

As listed in project description

Font styles to use
Serif

Requirements
Must have
• Large logo on back of card

```html
<!DOCTYPE html>
<html lang="en">
<head>
<meta charset="utf-8">
<title>Tovrin Business Card</title>
<link rel="stylesheet" href="https://fonts.googleapis.com/css2?family=Poppins:wght@400;500;700;800&display=swap">
<style>
  :root {
    --stage: #444444;
    --card-white: #fbfbfb;
    --brand-blue: #1f5fb3;
    --brand-sky: #3aa0dc;
    --ink: #3a3a3a;
    --deep-navy: #0d1f45;
    --photo-blue: #0b4a9c;
    --photo-dark: #10213f;
    --edge: #2668c4;
  }
  * { margin: 0; padding: 0; box-sizing: border-box; }
  html, body { width: 1200px; height: 801px; overflow: hidden; }
  body {
    background: var(--stage);
    font-family: "Poppins", Arial, sans-serif;
    position: relative;
  }
  .card {
    position: absolute;
    width: 525px;
    height: 300px;
    border-radius: 3px;
    box-shadow: 0 14px 30px rgba(0,0,0,0.35);
    overflow: hidden;
    border-bottom: 3px solid var(--edge);
  }
  /* Front side */
  .card-front {
    left: 45px;
    top: 250px;
    background: var(--card-white);
  }
  .front-brand {
    position: absolute;
    left: 42px;
    top: 96px;
    display: flex;
    align-items: center;
    gap: 9px;
  }
  .brand-square {
    width: 14px;
    height: 14px;
    background: var(--brand-sky);
  }
  .front-brand .brand-name {
    font-weight: 800;
    font-size: 36px;
    letter-spacing: 1px;
    color: var(--brand-blue);
    line-height: 1;
  }
  .address {
    position: absolute;
    left: 42px;
    top: 170px;
    font-size: 13px;
    line-height: 1.45;
    color: var(--ink);
  }
  .person {
    position: absolute;
    left: 278px;
    top: 62px;
  }
  .person-name {
    font-weight: 700;
    font-size: 25px;
    color: var(--brand-blue);
    line-height: 1.1;
  }
  .person-role {
    font-size: 16px;
    color: var(--brand-sky);
    margin-top: 2px;
  }
  .contact {
    position: absolute;
    left: 278px;
    top: 148px;
    display: flex;
    gap: 10px;
    align-items: stretch;
  }
  .contact-icons {
    width: 26px;
    background: var(--brand-blue);
    border-radius: 13px;
    display: flex;
    flex-direction: column;
    justify-content: space-around;
    align-items: center;
    padding: 6px 0;
  }
  .contact-icons svg { width: 13px; height: 13px; }
  .contact-list {
    list-style: none;
    font-size: 13px;
    line-height: 1.55;
    color: var(--ink);
  }
  /* Back side */
  .card-back {
    left: 630px;
    top: 250px;
  }
  .back-photo {
    position: absolute;
    inset: 0;
    background:
      radial-gradient(ellipse at 25% 80%, var(--photo-blue) 0%, rgba(11,74,156,0) 60%),
      linear-gradient(135deg, #0a3f86 0%, var(--photo-dark) 75%);
  }
  .back-brand {
    position: absolute;
    left: 0;
    right: 0;
    top: 50%;
    transform: translateY(-50%);
    display: flex;
    justify-content: center;
    align-items: center;
    gap: 12px;
  }
  .back-brand .brand-name {
    font-weight: 800;
    font-size: 64px;
    letter-spacing: 2px;
    color: #ffffff;
    line-height: 1;
  }
</style>
</head>
<body>

  <section class="card card-front">
    <div class="front-brand">
      <span class="brand-square"></span>
      <span class="brand-name">TOVRIN</span>
    </div>
    <p class="address">87 Marrow Ave,<br>Pendlebay, QLD, 4023</p>

    <div class="person">
      <h1 class="person-name">Warren Halbeck</h1>
      <p class="person-role">General Manager</p>
    </div>

    <div class="contact">
      <div class="contact-icons">
        <svg viewBox="0 0 16 16" aria-hidden="true"><path d="M4 1l3 3-2 2c1 2 3 4 5 5l2-2 3 3-2 2C7 15 1 9 2 3z" fill="#fff"/></svg>
        <svg viewBox="0 0 16 16" aria-hidden="true"><rect x="1" y="3" width="14" height="10" fill="none" stroke="#fff" stroke-width="1.6"/><path d="M1 3l7 6 7-6" fill="none" stroke="#fff" stroke-width="1.6"/></svg>
        <svg viewBox="0 0 16 16" aria-hidden="true"><circle cx="8" cy="8" r="6.5" fill="none" stroke="#fff" stroke-width="1.5"/><path d="M1.5 8h13M8 1.5c-3 3.5-3 9.5 0 13M8 1.5c3 3.5 3 9.5 0 13" fill="none" stroke="#fff" stroke-width="1.2"/></svg>
      </div>
      <ul class="contact-list">
        <li>0472 915 348</li>
        <li>Warren.halbeck@tovrin.com.au</li>
        <li>www.tovrin.com.au</li>
      </ul>
    </div>
  </section>

  <section class="card card-back">
    <div class="back-photo" role="img" aria-label="Blue-toned photo of a road roller compacting fresh asphalt with steam rising"></div>
    <div class="back-brand">
      <span class="brand-name">TOVRIN</span>
    </div>
  </section>

</body>
</html>
```